Brand new letterhead, business card, email signature etc.

We are a financial company in London, UK. Our website is www.marlowvane.com. We're wanting a complete remodel of the company colours, letter head, business cards, email signatures, etc. Looking to keep the same font for the company name. I have upload a colour palette that we want to work with. We're looking for company letterhead for outgoing letters/ correspondence, letterhead for internal documentation, email signatures, e-letters. etc. Ultimately we will redesign the entire website also. It is important that our clients get a strong, secure, warm, trustworthy, solid feeling and first impression.
Updates

Designs look the same

Target Market(s)

Institutional investors, (ultra) high net worth individuals

Industry/Entity Type

Finance, Invesments banking.

Font styles to use
Other font styles liked:
• Current font is "Champagne & Limousines"

Requirements
Must have
• Must use the colours provided on the PDF uploaded to the portal. The purple = main colour. The red = accent colour.
Nice to have
• Nice to use same font as now for the company name "Corvane". Font is "Champagne & Limousines". Nice to have some reference to the old logo flower, but only subtle.
Should not have
• Do not use the colour red from our website. Use the colours provided on the colour palette PDF that I uploaded in the portal.

```html
<!DOCTYPE html>
<html lang="en">
<head>
<meta charset="utf-8">
<title>Corvane Letterhead</title>
<link href="https://fonts.googleapis.com/css2?family=Lato:wght@300;400;700&family=Italianno&display=swap" rel="stylesheet">
<style>
  :root {
    --backdrop: #e9e9eb;
    --paper: #ffffff;
    --ink: #231a1e;
    --plum: #2e0f1b;
    --accent: #c0182f;
    --muted: #4a4346;
  }
  * { box-sizing: border-box; margin: 0; padding: 0; }
  html, body {
    width: 1200px; height: 874px; overflow: hidden;
    background: var(--backdrop);
  }
  .letterhead {
    position: absolute; left: 310px; top: 27px;
    width: 580px; height: 820px;
    background: var(--paper);
    overflow: hidden;
    font-family: 'Lato', sans-serif;
    color: var(--ink);
    box-shadow: 0 2px 10px rgba(0,0,0,0.08);
  }
  .brand {
    position: absolute; left: 40px; top: 62px;
    display: flex; align-items: center; gap: 20px;
  }
  .brand-square {
    width: 74px; height: 74px;
    border: 1px solid var(--plum);
  }
  .brand-name {
    font-family: 'Lato', sans-serif; font-weight: 300;
    font-size: 32px; letter-spacing: 11px; color: var(--ink);
  }
  .contact {
    position: absolute; right: 44px; top: 30px;
    display: flex; gap: 14px;
    font-family: 'Lato', sans-serif; font-weight: 300;
    font-size: 8.5px; line-height: 1.45; color: var(--muted);
  }
  .contact-rule { width: 1px; background: var(--ink); }
  .contact-list { list-style: none; }
  .contact-list li { display: flex; align-items: center; gap: 5px; }
  .contact-list svg { width: 7px; height: 7px; fill: var(--ink); }
  .contact-address { margin-top: 4px; }
  .recipient {
    position: absolute; left: 44px; top: 168px;
    font-size: 11.5px; line-height: 1.35;
  }
  .recipient p + p { margin-top: 9px; }
  .salutation {
    position: absolute; left: 44px; top: 284px;
    font-weight: 700; font-size: 15px;
  }
  .body-copy {
    position: absolute; left: 44px; top: 312px; width: 495px;
    font-size: 10.5px; line-height: 1.36;
  }
  .body-copy p + p { margin-top: 12px; }
  .closing {
    position: absolute; left: 44px; top: 578px; font-size: 11.5px;
  }
  .signature {
    position: absolute; left: 66px; top: 628px;
    font-family: 'Italianno', cursive; font-size: 44px; color: var(--ink);
  }
  .wave { position: absolute; inset: 0; width: 580px; height: 820px; }
</style>
</head>
<body>
  <main class="letterhead">
    <svg class="wave" viewBox="0 0 580 820" aria-hidden="true">
      <path d="M0 806 C 150 800, 300 790, 400 760 C 470 738, 530 700, 580 680 L580 820 L0 820 Z" fill="var(--plum)"/>
      <path d="M14 815 C 150 808, 280 797, 365 776" fill="none" stroke="#ffffff" stroke-width="2.5"/>
      <path d="M372 762 C 442 742, 522 702, 580 671" fill="none" stroke="var(--accent)" stroke-width="4.5"/>
    </svg>

    <header class="brand">
      <div class="brand-square"></div>
      <span class="brand-name">CORVANE</span>
    </header>

    <aside class="contact">
      <div class="contact-rule"></div>
      <div>
        <ul class="contact-list">
          <li><svg viewBox="0 0 10 10"><path d="M2 0 L4 2 L3 4 Q5 6 6 7 L8 6 L10 8 L8 10 Q0 8 0 2 Z"/></svg>123 456 789</li>
          <li><svg viewBox="0 0 10 10"><rect x="0" y="2" width="10" height="6"/></svg>info@marlowvane.com</li>
          <li><svg viewBox="0 0 10 10"><circle cx="5" cy="5" r="5"/></svg>www.marlowvane.com</li>
        </ul>
        <p class="contact-address">Corvane Group Limited<br>9th Floor 14 Harlow Yard<br>London EC2M 7QT</p>
      </div>
    </aside>

    <section class="recipient">
      <p>January-03-2020</p>
      <p>Mr. John Doe<br>President</p>
      <p>Link Corpration<br>123 Street Name, Suite# 10<br>City, State, 120023</p>
    </section>

    <h2 class="salutation">Dear Mr. John</h2>

    <article class="body-copy">
      <p>Lorem ipsum dolor sit amet, consectetur adipiscing elit, sed do eiusmod tempor incididunt ut labore et dolore magna aliqua. Ut enim ad minim veniam, quis nostrud exercitation ullamco laboris nisi ut aliquip ex ea commodo consequat. Duis aute irure dolor in reprehenderit in voluptate velit esse cillum dolore eu fugiat nulla pariatur.</p>
      <p>Lorem ipsum dolor sit amet, consectetur adipiscing elit, sed do eiusmod tempor incididunt ut labore et dolore magna aliqua. Ut enim ad minim veniam, quis nostrud exercitation ullamco laboris nisi ut aliquip ex ea commodo consequat. Duis aute irure dolor in reprehenderit in voluptate velit esse cillum dolore eu fugiat nulla pariatur.</p>
      <p>Lorem ipsum dolor sit amet, consectetur adipiscing elit, sed do eiusmod tempor incididunt ut labore et dolore magna aliqua. Ut enim ad minim veniam, quis nostrud exercitation ullamco laboris nisi ut aliquip ex ea commodo consequat.</p>
      <p>Excepteur sint occaecat cupidatat non proident, sunt in culpa qui officia deserunt mollit anim id est laborum. re et dolore magnam aliquam quaerat voluptatem.</p>
    </article>

    <p class="closing">Regards</p>
    <p class="signature">Edwin Carrow</p>
  </main>
</body>
</html>
```